Website for Excavator and Earthworks Company

We require a modern, sleek and practical website for our newly created earthworks/excavator business in Perth, Western Australia called Bluegum Ridge Earthworks.

The website should have a modern, cutting edge feel but only needs to be relatively simplistic in it's layout and eventual functionality.

Some pages it should have would be Home, About, Projects and Contact Us.

```html
<!DOCTYPE html>
<html lang="en">
<head>
<meta charset="utf-8">
<title>Bluegum Ridge Earthworks</title>
<link rel="stylesheet" href="https://fonts.googleapis.com/css2?family=Chakra+Petch:wght@500;600;700&family=Figtree:wght@400;500;600&display=swap">
<style>
:root{
  --lime:#cddc00;
  --ink:#111111;
  --muted:#4a4a4a;
  --gray:#f4f4f4;
  --night:#0d1522;
  --white:#ffffff;
  --line:#e2e2e2;
}
*{box-sizing:border-box;margin:0;padding:0}
html,body{width:1200px;height:3589px;overflow:hidden}
body{position:relative;font-family:"Figtree",sans-serif;color:var(--ink);background:var(--white)}
.abs{position:absolute}
.heading{font-family:"Chakra Petch",sans-serif;font-weight:600;text-transform:uppercase;letter-spacing:.5px}
.pill{position:absolute;display:flex;align-items:center;gap:7px;border-radius:20px;font-size:12px;font-weight:500;text-transform:uppercase;padding:0 20px;height:31px}
.pill::before{content:"";width:5px;height:5px;border-radius:50%;background:var(--lime)}
.pill-light{border:1px solid #d7d7d7;color:var(--ink);background:var(--white)}
.pill-dark{border:1px solid rgba(255,255,255,.55);color:var(--white)}
.btn{position:absolute;display:flex;align-items:center;height:38px;border-radius:20px;font-size:12.5px;font-weight:600;text-transform:uppercase}
.btn .label{height:38px;display:flex;align-items:center;padding:0 26px;border-radius:20px}
.btn .go{width:34px;height:34px;border-radius:50%;margin-left:-8px;display:flex;align-items:center;justify-content:center}
.btn-lime .label{background:var(--lime);color:var(--ink)}
.btn-lime .go{background:var(--ink)}
.btn-white .label{background:var(--white);color:var(--ink)}
.btn-white .go{background:var(--lime)}
.btn-lime-w .go{background:var(--white)}
/* header */
.site-header{position:absolute;left:0;top:0;width:1200px;height:91px;background:var(--white)}
.brand{position:absolute;display:flex;align-items:center;gap:10px}
.brand-mark{width:34px;height:34px;background:var(--lime)}
.brand-name{font-family:"Chakra Petch",sans-serif;font-weight:700;font-size:17px;line-height:1.05;color:var(--ink);text-transform:uppercase;letter-spacing:.5px}
.nav{position:absolute;display:flex;font-size:12.5px;font-weight:500;text-transform:uppercase}
.call{position:absolute;left:752px;top:26px;display:flex;align-items:center;gap:8px}
.call-icon{width:34px;height:34px;border-radius:50%;background:var(--lime);display:flex;align-items:center;justify-content:center}
.call small{display:block;font-size:10px;text-transform:uppercase}
.call strong{font-size:15px;font-weight:600}
.divider{position:absolute;left:725px;top:24px;width:1px;height:44px;background:var(--line)}
/* hero */
.hero{position:absolute;left:0;top:91px;width:1200px;height:694px;background:linear-gradient(180deg,#3a1d22 0%,#b2423b 22%,#d9774a 40%,#5a3a26 62%,#1f1612 100%)}
.hero-shade{position:absolute;inset:0;background:linear-gradient(90deg,rgba(15,10,8,.8) 0%,rgba(15,10,8,.45) 45%,rgba(15,10,8,0) 70%)}
.hero h1{position:absolute;left:141px;top:203px;font-size:53px;line-height:63px;color:var(--white)}
.hero p{position:absolute;left:141px;top:333px;width:460px;font-size:16px;line-height:29px;color:var(--white)}
.cut{position:absolute;left:0;top:740px}
/* services */
.card{position:absolute;top:881px;width:206px;height:195px;border:2px solid #e6ef8a;background:var(--white);box-shadow:0 6px 18px rgba(0,0,0,.05);padding:26px 14px}
.card.active{background:var(--lime);border:4px solid #d9e642;top:876px;height:205px}
.card .icon{width:40px;height:36px;margin-bottom:24px}
.card h3{font-size:15px;margin-bottom:10px}
.card p{font-size:11.5px;line-height:21px;color:var(--muted)}
.card.active p{color:var(--ink)}
/* about */
.about{position:absolute;left:0;top:1172px;width:1200px;height:676px;background:var(--gray)}
.frame-line{position:absolute;background:var(--lime)}
.about-photo{position:absolute;left:151px;top:1274px;width:418px;height:481px;background:linear-gradient(160deg,#7fa7c6 0%,#e7b070 40%,#d98a3a 62%,#4a3322 100%)}
.badge{position:absolute;left:461px;top:1528px;width:144px;height:155px;background:var(--lime);padding:16px 19px}
.badge strong{display:block;font-family:"Chakra Petch",sans-serif;font-weight:600;font-size:32px;margin-top:8px;line-height:1.1}
.badge span{display:block;font-family:"Chakra Petch",sans-serif;font-weight:600;font-size:14px;line-height:19px;text-transform:uppercase}
.about h2{position:absolute;left:672px;top:1330px;font-size:34px}
.about-copy{position:absolute;left:672px;top:1382px;width:385px;font-size:11.5px;line-height:22.6px;color:var(--muted)}
.about-copy p+p{margin-top:7px}
/* projects */
.projects h2{position:absolute;left:0;width:1200px;top:1980px;text-align:center;font-size:34px}
.tile{position:absolute}
/* contact */
.contact-bg{position:absolute;left:0;top:2690px}
.contact h2{position:absolute;left:141px;top:2888px;font-size:34px;color:var(--white)}
.contact .lead{position:absolute;left:141px;top:2950px;width:420px;font-size:12px;line-height:21px;color:var(--white)}
.info{position:absolute;left:141px;display:flex;gap:14px;color:var(--white)}
.info .ico{width:50px;height:40px;display:flex;align-items:center;justify-content:center}
.info b{display:block;font-size:12.5px;font-weight:500;margin-bottom:3px}
.info span{display:block;font-size:12px;line-height:18px;color:#dcdcdc}
.social{position:absolute;left:141px;top:3241px;display:flex;gap:10px}
.social span{width:30px;height:30px;border-radius:50%;border:1px solid var(--white)}
.social span.on{background:var(--lime);border-color:var(--lime)}
.form{position:absolute;left:629px;top:2817px;width:430px;height:504px;background:var(--white);padding:0 30px}
.form h3{text-align:center;font-size:28px;margin:30px 0 22px}
.field{position:relative;margin-bottom:17px}
.field label{display:block;font-size:12px;font-weight:500;padding-left:17px;margin-bottom:-2px}
.field .box{height:48px;border:1px solid var(--line);border-top:none;border-radius:0 0 4px 4px;padding:0 16px;display:flex;align-items:center;justify-content:space-between;font-size:12px;color:#777}
.field .box.tall{height:97px;align-items:flex-start;padding-top:12px}
.submit{margin-top:24px;height:44px;border-radius:22px;background:var(--lime);display:flex;align-items:center;justify-content:center;font-size:13px;font-weight:600;letter-spacing:1.5px;text-transform:uppercase}
/* footer */
.footer-line{position:absolute;left:141px;top:3529px;width:918px;height:1px;background:var(--line)}
.copy{position:absolute;left:0;width:1200px;top:3549px;text-align:center;font-size:12px}
</style>
</head>
<body>
<svg width="0" height="0" style="position:absolute">
  <symbol id="arrow" viewBox="0 0 16 16"><path d="M4 12 L12 4 M6 4 H12 V10" fill="none" stroke="currentColor" stroke-width="1.6"/></symbol>
</svg>

<header class="site-header">
  <div class="brand" style="left:141px;top:27px">
    <span class="brand-mark"></span>
    <span class="brand-name">Bluegum Ridge<br>Earthworks</span>
  </div>
  <nav class="nav" style="left:477px;top:37px;gap:34px">
    <span>Home</span><span>About Us</span><span>Projects</span>
  </nav>
  <div class="divider"></div>
  <div class="call">
    <span class="call-icon"><svg width="16" height="16" viewBox="0 0 24 24"><path d="M6.6 10.8a15 15 0 0 0 6.6 6.6l2.2-2.2a1 1 0 0 1 1-.25 11.4 11.4 0 0 0 3.6.6 1 1 0 0 1 1 1V20a1 1 0 0 1-1 1A17 17 0 0 1 3 4a1 1 0 0 1 1-1h3.5a1 1 0 0 1 1 1c0 1.25.2 2.45.6 3.6a1 1 0 0 1-.25 1z" fill="none" stroke="#111" stroke-width="1.6"/></svg></span>
    <span><small>Call us now</small><strong>(08) 5550 1427</strong></span>
  </div>
  <div class="btn btn-lime" style="left:914px;top:25px">
    <span class="label">Contact Us</span><span class="go" style="color:#fff"><svg width="13" height="13"><use href="#arrow"/></svg></span>
  </div>
</header>

<section class="hero" role="img" aria-label="Excavator working on a dirt mound under a red sunset sky">
  <div class="hero-shade"></div>
</section>
<svg class="cut" width="1200" height="48" viewBox="0 0 1200 48"><polygon points="574,45 632,3 1200,3 1200,48 574,48" fill="#fff"/></svg>
<div class="pill pill-dark" style="left:141px;top:240px;height:36px;font-size:11.5px">Perth's Trusted Earthworks Experts</div>
<h1 class="heading abs" style="left:141px;top:294px;font-size:53px;line-height:63px;color:#fff">Moving Earth,<br>Building Futures</h1>
<p class="abs" style="left:141px;top:424px;width:460px;font-size:16px;line-height:29px;color:#fff">Professional Excavation, Site Preparation, And Earthmoving Services Across Perth And Western Australia. Quality Work, Delivered On Time.</p>
<div class="btn btn-lime btn-lime-w" style="left:141px;top:533px">
  <span class="label">Start Your Project</span><span class="go" style="color:#111"><svg width="13" height="13"><use href="#arrow"/></svg></span>
</div>
<div class="btn btn-white" style="left:357px;top:533px">
  <span class="label">Get Quote</span><span class="go" style="color:#111"><svg width="13" height="13"><use href="#arrow"/></svg></span>
</div>

<section class="services">
  <div class="card" style="left:145px">
    <div class="icon" role="img" aria-label="Building icon"><svg width="40" height="36"><rect x="4" y="4" width="32" height="30" fill="#111"/></svg></div>
    <h3 class="heading">Site Preparation</h3>
    <p>Complete Clearing And Leveling For Construction Projects</p>
  </div>
  <div class="card active" style="left:375px;width:217px">
    <div class="icon" role="img" aria-label="Excavator icon"><svg width="40" height="36"><rect x="4" y="4" width="32" height="30" fill="#111"/></svg></div>
    <h3 class="heading">Excavation</h3>
    <p>Precision Digging For Foundations, Pools, And Utilities</p>
  </div>
  <div class="card" style="left:615px">
    <div class="icon" role="img" aria-label="Bulldozer icon"><svg width="40" height="36"><rect x="4" y="4" width="32" height="30" fill="#111"/></svg></div>
    <h3 class="heading">Land Clearing</h3>
    <p>Efficient Removal Of Vegetation And Debris</p>
  </div>
  <div class="card" style="left:849px">
    <div class="icon" role="img" aria-label="Trench icon"><svg width="40" height="36"><rect x="4" y="4" width="32" height="30" fill="#111"/></svg></div>
    <h3 class="heading">Trenching</h3>
    <p>Safe Trenching For Pipes, Cables, And Drainage</p>
  </div>
</section>

<section class="about">
</section>
<div class="frame-line" style="left:141px;top:1265px;width:176px;height:5px"></div>
<div class="frame-line" style="left:141px;top:1265px;width:5px;height:344px"></div>
<div class="about-photo" role="img" aria-label="Yellow excavator lifting soil at sunset"></div>
<svg class="abs" style="left:370px;top:1730px" width="200" height="26"><polygon points="0,26 30,0 200,0 200,26" fill="#f4f4f4"/></svg>
<div class="badge">
  <svg width="34" height="34" viewBox="0 0 34 34"><circle cx="17" cy="14" r="11" fill="none" stroke="#111" stroke-width="2.5"/><circle cx="17" cy="14" r="5" fill="#111"/><path d="M10 23 L8 33 L17 29 L26 33 L24 23" fill="none" stroke="#111" stroke-width="2.5"/></svg>
  <strong>15+</strong>
  <span>Years Of<br>Excellence</span>
</div>
<div class="pill pill-light" style="left:672px;top:1288px">Who We Are</div>
<h2 class="heading abs" style="left:672px;top:1328px;font-size:34px">About Bluegum Ridge</h2>
<div class="about-copy" style="top:1381px">
  <p>Bluegum Ridge Earthworks Is A Locally Owned And Operated Earthmoving Company Serving Perth And Surrounding Areas. With Over 15 Years Of Experience, We've Built Our Reputation On Reliability, Precision, And Exceptional Customer Service.</p>
  <p>Lorem Ipsum Is Simply Dummy Text Of The Printing And Typesetting Industry. Lorem Ipsum Has Been The Industry's Standard Dummy Text Ever Since The 1500s, When An Unknown Printer Took A Galley Of Type And Scrambled It To Make A Type Specimen Book. It Has Survived Not Only Five Centuries, But Also The Leap Into Electronic Typesetting, Remaining Essentially Unchanged. It Was Popularised In The 1960s With The Release Of Letraset Sheets Containing Lorem Ipsum Passages, And More Recently With Desktop.</p>
</div>
<div class="btn btn-lime" style="left:672px;top:1684px">
  <span class="label">Read More</span><span class="go" style="color:#fff"><svg width="13" height="13"><use href="#arrow"/></svg></span>
</div>

<section class="projects">
  <div class="pill pill-light" style="left:527px;top:1940px">Work Gallery</div>
  <h2 class="heading" style="top:1982px">Out Projects</h2>
  <div class="tile" style="left:141px;top:2046px;width:241px;height:194px;background:linear-gradient(180deg,#4a6b8f,#d58a45 60%,#3a2b20)" role="img" aria-label="Excavator at dusk"></div>
  <div class="tile" style="left:141px;top:2243px;width:241px;height:280px;background:linear-gradient(160deg,#4c5056,#6b6f72 50%,#a88a3a 80%,#2e2e2e)" role="img" aria-label="Loader filling a dump truck in a quarry"></div>
  <div class="tile" style="left:385px;top:2046px;width:404px;height:299px;background:linear-gradient(180deg,#3d6c9c,#9cb6c8 35%,#e6a24a 55%,#5a4a36 80%,#3a2e22)" role="img" aria-label="Excavator and loader on a site at sunrise"></div>
  <div class="tile" style="left:385px;top:2348px;width:117px;height:175px;background:linear-gradient(180deg,#8a7e6e,#b89a6c 50%,#5e4a34)" role="img" aria-label="Machine bucket pouring soil"></div>
  <div class="tile" style="left:504px;top:2348px;width:285px;height:175px;background:linear-gradient(180deg,#2f6fc4,#7eaee0 40%,#c49a5a 70%,#8a5a34)" role="img" aria-label="Excavator loading a truck under blue sky"></div>
  <div class="tile" style="left:791px;top:2046px;width:267px;height:194px;background:linear-gradient(180deg,#405a7a,#a7998a 45%,#c89445 70%,#4a3828)" role="img" aria-label="Backhoe loader on a work site"></div>
  <div class="tile" style="left:791px;top:2243px;width:267px;height:280px;background:linear-gradient(180deg,#3b84c8,#8dbde6 45%,#c8a45a 70%,#8a6440)" role="img" aria-label="Yellow excavator digging soil"></div>
  <div class="btn btn-lime" style="left:489px;top:2559px">
    <span class="label">Discuss Your Project</span><span class="go" style="color:#fff"><svg width="13" height="13"><use href="#arrow"/></svg></span>
  </div>
</section>

<section class="contact">
  <svg class="contact-bg" width="1200" height="718" viewBox="0 0 1200 718" role="img" aria-label="Excavators on a dark site at night">
    <defs><linearGradient id="night" x1="0" y1="0" x2="1" y2="1"><stop offset="0" stop-color="#0f1826"/><stop offset=".5" stop-color="#101a27"/><stop offset="1" stop-color="#1c2230"/></linearGradient></defs>
    <polygon points="0,0 576,0 634,42 1200,42 1200,718 0,718" fill="url(#night)"/>
  </svg>
  <div class="pill pill-dark" style="left:141px;top:2848px">Contact</div>
  <h2 class="heading">Contact Details</h2>
  <p class="lead">Lorem Ipsum Odor Amet, Consectetuer Adipiscing Elit. Cubilia Montes Libero Sagittis Torquent Purus Platea.Facilisi Donec .</p>
  <div class="info" style="top:3018px">
    <span class="ico"><svg width="34" height="38" viewBox="0 0 34 38"><circle cx="12" cy="22" r="12" fill="#5f6a00" opacity=".6"/><rect x="12" y="4" width="16" height="32" fill="none" stroke="#cddc00" stroke-width="2"/><path d="M16 10h8M16 16h8M16 22h8M16 28h8" stroke="#cddc00" stroke-width="2"/></svg></span>
    <div><b>Location</b><span>123 Lorem Ipsum Odor Ametconsectetuer<br>Adipiscing Elit. Cubilia Montes.</span></div>
  </div>
  <div class="info" style="top:3100px">
    <span class="ico"><svg width="36" height="36" viewBox="0 0 36 36"><circle cx="12" cy="22" r="12" fill="#5f6a00" opacity=".6"/><rect x="6" y="12" width="26" height="20" fill="none" stroke="#cddc00" stroke-width="2"/><path d="M6 12l13 11 13-11" fill="none" stroke="#cddc00" stroke-width="2"/></svg></span>
    <div><b>Email Address</b><span>hello@bluegumridge.example</span></div>
  </div>
  <div class="info" style="top:3170px">
    <span class="ico"><svg width="36" height="36" viewBox="0 0 24 24"><circle cx="8" cy="15" r="8" fill="#5f6a00" opacity=".6"/><path d="M6.6 10.8a15 15 0 0 0 6.6 6.6l2.2-2.2a1 1 0 0 1 1-.25 11.4 11.4 0 0 0 3.6.6 1 1 0 0 1 1 1V20a1 1 0 0 1-1 1A17 17 0 0 1 3 4a1 1 0 0 1 1-1h3.5a1 1 0 0 1 1 1c0 1.25.2 2.45.6 3.6a1 1 0 0 1-.25 1z" fill="none" stroke="#cddc00" stroke-width="1.4"/></svg></span>
    <div><b>Phone Number</b><span style="font-size:15px;color:#fff">(08) 5550 1427</span></div>
  </div>
  <div class="social" aria-label="Social links">
    <span></span><span class="on"></span><span></span><span></span>
  </div>
  <form class="form">
    <h3 class="heading">Quick Inquiry</h3>
    <div class="field"><label>Full Name</label><div class="box"><span>Enter Your Name</span><svg width="12" height="12" viewBox="0 0 12 12"><circle cx="6" cy="3.5" r="2.5" fill="#999"/><path d="M1 12a5 5 0 0 1 10 0z" fill="#999"/></svg></div></div>
    <div class="field"><label>Phone No</label><div class="box"><span>(08) 5550 1427</span><svg width="12" height="12" viewBox="0 0 24 24"><path d="M6.6 10.8a15 15 0 0 0 6.6 6.6l2.2-2.2a1 1 0 0 1 1-.25 11.4 11.4 0 0 0 3.6.6 1 1 0 0 1 1 1V20a1 1 0 0 1-1 1A17 17 0 0 1 3 4a1 1 0 0 1 1-1h3.5a1 1 0 0 1 1 1c0 1.25.2 2.45.6 3.6a1 1 0 0 1-.25 1z" fill="#999"/></svg></div></div>
    <div class="field"><label>Email Address</label><div class="box"><span>info@bluegumridge.example</span><svg width="14" height="11" viewBox="0 0 14 11"><rect width="14" height="11" rx="1" fill="#999"/><path d="M1 1l6 5 6-5" fill="none" stroke="#fff" stroke-width="1.2"/></svg></div></div>
    <div class="field"><label>Message</label><div class="box tall"><span>Type Your Message Here!</span><svg width="13" height="13" viewBox="0 0 13 13"><circle cx="6.5" cy="6.5" r="6" fill="#999"/></svg></div></div>
    <div class="submit">Submit Now</div>
  </form>
</section>

<footer>
  <div class="brand" style="left:141px;top:3448px">
    <span class="brand-mark"></span>
    <span class="brand-name">Bluegum Ridge<br>Earthworks</span>
  </div>
  <nav class="nav" style="left:629px;top:3460px;gap:64px">
    <span>Home</span><span>About Us</span><span>Projects</span><span>Contact Us</span>
  </nav>
  <div class="footer-line"></div>
  <p class="copy">© 2026 Bluegum Ridge. All Rights Reserved.</p>
</footer>
</body>
</html>
```